Glimmer Step Blog

Need a blog design. I am the first GlimStep blogger-very exciting! My first project will be reporting on Twirling Under Lanterns which premieres this Monday-St. Patrick's Day. I am looking for an exciting format to represent my new venture. I will be focusing on ballroom dance fashion-I like creativity and look for something with a cool color scheme, artistic, could be modern or really open for someone to interpret this concept in a creative way. The blog name is GlimStep.

Fashion

```html
<!DOCTYPE html>
<html lang="en">
<head>
<meta charset="utf-8">
<title>GlimStep – Glimmer Step Blog</title>
<link rel="stylesheet" href="https://fonts.googleapis.com/css2?family=Montserrat:wght@600;700;800&family=Open+Sans:wght@400;600&family=Great+Vibes&display=swap">
<style>
:root{
  --red:#f4412e;
  --ink:#2b2b2b;
  --text:#6f6f6f;
  --muted:#8a8a8a;
  --line:#e4e4e4;
  --panel:#ffffff;
  --tab:#e6e6e6;
  --dark:#1f1f1f;
  --link:#3b5998;
}
*{box-sizing:border-box;margin:0;padding:0}
html,body{width:1200px;height:2483px;overflow:hidden;background:#fff}
body{position:relative;font-family:"Open Sans",Arial,sans-serif;color:var(--text)}

/* header */
.site-header{position:absolute;top:0;left:0;width:1200px;height:50px}
.brand{position:absolute;left:187px;top:8px;font-family:"Montserrat",sans-serif;font-weight:700;font-size:29px;color:var(--ink);letter-spacing:.5px}
.social{position:absolute;left:912px;top:16px;display:flex;gap:10px}
.social span{width:17px;height:17px;background:var(--ink);display:block}

/* hero */
.hero{position:absolute;top:50px;left:0;width:1200px;height:455px;
  background:linear-gradient(90deg,#3a3a3a 0%,#6d6d6d 35%,#8a7b82 55%,#b46b8f 62%,#555 78%,#2f2f2f 100%)}
.hero-date{position:absolute;left:187px;top:108px;background:#444;color:#ddd;font-size:11px;padding:3px 14px;letter-spacing:.3px}
.hero-title{position:absolute;left:187px;top:144px;font-family:"Montserrat",sans-serif;font-weight:800;font-size:27px;line-height:31px;color:#fff;text-transform:uppercase;white-space:nowrap;letter-spacing:-.2px}
.hero-sub{position:absolute;left:187px;top:210px;width:360px;font-size:15px;line-height:18px;color:#fff}
.hero-btn{position:absolute;left:187px;top:263px;width:238px;height:43px;background:var(--red);color:#fff;font-family:"Montserrat",sans-serif;font-weight:700;font-size:14px;display:flex;align-items:center;justify-content:center}
.hero-arrow{position:absolute;top:174px;width:36px;height:36px;border-radius:50%;background:rgba(255,255,255,.35)}
.hero-arrow svg{display:block}
.hero-arrow.prev{left:126px}
.hero-arrow.next{left:1037px}

/* posts */
.posts{position:absolute;left:187px;top:575px;width:553px}
.post-title{font-family:"Open Sans",sans-serif;font-weight:600;font-size:26px;line-height:33px;color:var(--ink);letter-spacing:-.5px;white-space:nowrap}
.post-meta{margin-top:12px;font-size:11px;color:var(--muted);display:flex;gap:18px;align-items:center}
.post-meta .comments{display:flex;align-items:center;gap:5px}
.post-image{margin-top:14px;width:551px;height:282px}
.post-body{margin-top:22px}
.post-body p{font-size:12px;line-height:15px;color:var(--text)}
.post-body p+p{margin-top:14px}
.post-footer{margin-top:22px;border-top:1px solid var(--line);padding-top:8px;height:34px;display:flex;justify-content:space-between;align-items:center}
.share{display:flex;gap:6px;font-size:9px;color:#555}
.share .btn{border:1px solid #ccc;padding:0 5px;height:14px;line-height:12px;border-radius:2px;background:#f4f4f4}
.share .count{border:1px solid #ccc;padding:0 4px;height:14px;line-height:12px}
.read-more{color:var(--red);font-size:12.5px;display:flex;align-items:center;gap:6px}
.divider{border:0;border-top:2px dotted #777;margin:16px 0 34px;width:553px}

.img-party{background:linear-gradient(135deg,#2b3a6e,#5a3f6a 40%,#b24a3a 75%,#3b2a25)}
.img-stage{background:linear-gradient(135deg,#c8304a,#6a2d6e 40%,#2c4f9a 70%,#1c1c2b)}
.img-ballroom{background:linear-gradient(90deg,#2e2e2e,#7a7a7a 40%,#b9698e 55%,#444 80%,#2a2a2a)}

/* sidebar */
.sidebar{position:absolute;left:773px;top:566px;width:240px}
.widget{background:var(--panel);border:1px solid var(--line);border-radius:3px}
.tabs{display:flex;padding:13px 10px 0 10px}
.tab{flex:1;height:40px;display:flex;align-items:center;justify-content:center;font-size:17px;color:var(--ink)}
.tab.inactive{background:var(--tab);color:#777}
.news{padding:14px 14px 0 24px}
.news-item{display:flex;gap:10px;padding:10px 0 13px;border-bottom:1px solid var(--line)}
.news-item:last-child{border-bottom:0}
.news-thumb{width:60px;height:46px;flex:none;border:2px solid #ddd}
.news-date{font-size:10px;font-style:italic;color:var(--muted)}
.news-text{font-size:11px;line-height:14px;color:var(--ink)}
.widget-link{color:var(--red);font-size:12px;display:flex;align-items:center;gap:6px;padding:10px 0 24px 24px}

.welcome{margin-top:23px;height:374px;padding:30px 24px 0}
.welcome-title{font-family:"Great Vibes",cursive;font-size:34px;line-height:40px;color:var(--ink)}
.welcome p{margin-top:18px;font-size:12.5px;line-height:18px;color:var(--text)}
.welcome .widget-link{padding:14px 0 0 0}

.fb{margin-top:48px;height:320px}
.fb-head{background:var(--dark);color:#fff;height:46px;display:flex;align-items:center;padding-left:24px;font-size:14px}
.fb-page{display:flex;gap:10px;padding:14px 0 0 24px}
.fb-mark{width:36px;height:36px;background:#f0f0f0}
.fb-name{font-size:11px;font-weight:600;color:var(--link)}
.fb-like{margin-top:3px;font-size:9px;border:1px solid #bbb;padding:0 5px;display:inline-block;color:#444}
.fb-count{padding:12px 24px 0;font-size:8.5px;color:#555}
.fb-count b{font-weight:400;color:var(--link)}
.fb-faces{display:grid;grid-template-columns:repeat(4,40px);column-gap:10px;row-gap:8px;padding:8px 0 0 21px}
.face{width:40px;height:38px}
.face-name{font-size:7.5px;color:#333;margin-top:2px;white-space:nowrap}
.fb-foot{margin:10px 21px 0;border-top:1px solid var(--line);padding-top:8px;font-size:8.5px;color:#555;display:flex;gap:6px;align-items:center}
.fb-foot i{width:9px;height:9px;background:var(--link);display:block}

/* footer */
.site-footer{position:absolute;left:0;top:2433px;width:1200px;height:50px;background:var(--red)}
.site-footer .copy{position:absolute;left:187px;top:17px;font-size:11.5px;color:#fff}
.site-footer .social{top:16px;left:913px}
.site-footer .social span{background:rgba(255,255,255,.3)}
</style>
</head>
<body>

<header class="site-header">
  <div class="brand">GlimStep</div>
  <nav class="social" aria-label="Social links"><span></span><span></span><span></span><span></span></nav>
</header>

<section class="hero" role="img" aria-label="Black and white ballroom scene with a couple dancing, the woman in a pink gown">
  <div class="hero-date">Dated : 17 March 2014</div>
  <h1 class="hero-title">Dean Hart on Sunup's<br>Ultimate Gala Party</h1>
  <p class="hero-sub">Lorem ipsum dolor sit ametconsectetur adipiscing elit. In fermentum dolor non</p>
  <div class="hero-btn">See His Gala Party Dance</div>
  <div class="hero-arrow prev"><svg width="36" height="36" viewBox="0 0 36 36"><path d="M21 11 L13 18 L21 25" stroke="#fff" stroke-width="3" fill="none"/></svg></div>
  <div class="hero-arrow next"><svg width="36" height="36" viewBox="0 0 36 36"><path d="M15 11 L23 18 L15 25" stroke="#fff" stroke-width="3" fill="none"/></svg></div>
</section>

<main class="posts">
  <article class="post">
    <h2 class="post-title">Dolor sit amet, consec tetur adipiscing elit.</h2>
    <div class="post-meta"><span>March 17, 2014,</span><span class="comments"><svg width="11" height="10" viewBox="0 0 11 10"><path d="M1 1h9v6H5l-3 2V7H1z" fill="#666"/></svg>5 Comments</span></div>
    <div class="post-image img-party" role="img" aria-label="Group photo of dancers posing on a party stage"></div>
    <div class="post-body">
      <p>Lorem ipsum dolor sit amet, consectetur adipiscing elit. In fermentum dolor non augue pretium egestas. Donec sem eros, tincidunt at congue ut, posuere sit amet est. Vivamus scelerisque viverra odio sit amet laoreet. Ut nec neque non justo rutrum tempor lobortis eu ante.</p>
      <p>Aliquam sagittis, nibh quis commodo auctor, risus mauris laoreet lectus, id facilisis libero odio nec enim. Sed id ligula adipiscing purus lacinia aliquet. Sed eu est non nisl vehicula bibendum congue sit amet enim.</p>
    </div>
    <div class="post-footer">
      <div class="share"><span class="btn">Like</span><span class="count">3k</span><span class="btn">Post</span><span class="count">316</span><span class="btn">+1</span><span class="count">56</span></div>
      <span class="read-more">Continue Reading <svg width="12" height="8" viewBox="0 0 12 8"><path d="M0 4h10M7 1l3 3-3 3" stroke="#f4412e" stroke-width="1.5" fill="none"/></svg></span>
    </div>
  </article>
  <hr class="divider">

  <article class="post">
    <h2 class="post-title">Lorem ipsum dolor sit amet, consectetur adipis<br>cing elit Aliquam sagittis</h2>
    <div class="post-meta"><span>March 17, 2014,</span><span class="comments"><svg width="11" height="10" viewBox="0 0 11 10"><path d="M1 1h9v6H5l-3 2V7H1z" fill="#666"/></svg>5 Comments</span></div>
    <div class="post-image img-stage" role="img" aria-label="Colourful troupe of dancers performing on a lit stage"></div>
    <div class="post-body">
      <p>Lorem ipsum dolor sit amet, consectetur adipiscing elit. In fermentum dolor non augue pretium egestas. Donec sem eros, tincidunt at congue ut, posuere sit amet est. Vivamus scelerisque viverra odio sit amet laoreet. Ut nec neque non justo rutrum tempor lobortis eu ante.</p>
      <p>Aliquam sagittis, nibh quis commodo auctor, risus mauris laoreet lectus, id facilisis libero odio nec enim. Sed id ligula adipiscing purus lacinia aliquet. Sed eu est non nisl vehicula bibendum congue sit amet enim.</p>
    </div>
    <div class="post-footer">
      <div class="share"><span class="btn">Like</span><span class="count">3k</span><span class="btn">Post</span><span class="count">316</span><span class="btn">+1</span><span class="count">56</span></div>
      <span class="read-more">Continue Reading <svg width="12" height="8" viewBox="0 0 12 8"><path d="M0 4h10M7 1l3 3-3 3" stroke="#f4412e" stroke-width="1.5" fill="none"/></svg></span>
    </div>
  </article>
  <hr class="divider">

  <article class="post">
    <h2 class="post-title">Dolor sit amet, consec tetur adipiscing elit.</h2>
    <div class="post-meta"><span>March 17, 2014,</span><span class="comments"><svg width="11" height="10" viewBox="0 0 11 10"><path d="M1 1h9v6H5l-3 2V7H1z" fill="#666"/></svg>5 Comments</span></div>
    <div class="post-image img-ballroom" role="img" aria-label="Black and white ballroom with a couple dancing, the woman in a pink gown"></div>
    <div class="post-body">
      <p>Lorem ipsum dolor sit amet, consectetur adipiscing elit. In fermentum dolor non augue pretium egestas. Donec sem eros, tincidunt at congue ut, posuere sit amet est. Vivamus scelerisque viverra odio sit amet laoreet. Ut nec neque non justo rutrum tempor lobortis eu ante. Aliquam sagittis, nibh quis commodo auctor, risus mauris laoreet lectus, id facilisis libero odio nec enim. Sed id ligula adipiscing purus lacinia aliquet.</p>
    </div>
    <div class="post-footer">
      <div class="share"><span class="btn">Like</span><span class="count">3k</span><span class="btn">Post</span><span class="count">316</span><span class="btn">+1</span><span class="count">56</span></div>
      <span class="read-more">Continue Reading <svg width="12" height="8" viewBox="0 0 12 8"><path d="M0 4h10M7 1l3 3-3 3" stroke="#f4412e" stroke-width="1.5" fill="none"/></svg></span>
    </div>
  </article>
</main>

<aside class="sidebar">
  <section class="widget news-widget">
    <div class="tabs"><div class="tab">Top News</div><div class="tab inactive">Events</div></div>
    <div class="news">
      <div class="news-item"><div class="news-thumb" style="background:linear-gradient(135deg,#6b4a3a,#c98a5a)" role="img" aria-label="Dancers on stage"></div><div><div class="news-date">March, 172014</div><div class="news-text">Lorem ipsum dolor sit amet, consec tetur adip adipis cing elit...</div></div></div>
      <div class="news-item"><div class="news-thumb" style="background:linear-gradient(135deg,#1c1c1c,#a04040)" role="img" aria-label="Dancers under stage lights"></div><div><div class="news-date">March, 172014</div><div class="news-text">Consectetur adipiscing elit.tempor lobortis eu ante augue est...</div></div></div>
      <div class="news-item"><div class="news-thumb" style="background:linear-gradient(135deg,#3a3a3a,#b06a8a)" role="img" aria-label="Ballroom couple"></div><div><div class="news-date">March, 172014</div><div class="news-text">Lorem ipsum dolor sit amet, consec tetu...</div></div></div>
    </div>
    <div class="widget-link">Read All News <svg width="12" height="8" viewBox="0 0 12 8"><path d="M0 4h10M7 1l3 3-3 3" stroke="#f4412e" stroke-width="1.5" fill="none"/></svg></div>
  </section>

  <section class="widget welcome">
    <h3 class="welcome-title">Welcome to<br>GlimStep</h3>
    <p>Lorem ipsum dolor sit amet, consec tetur adipiscing elit. In fermentum dolor non augue pretium egestas. Donec sem eros, tincidunt at congue ut, posuere sit amet est. Vivamus scelerisque viverra odio sit amet laoreet. Ut nec neque non justo rutrum tempor lobortis eu ante. Aliquam sagittis, nibh quis commodo auctor</p>
    <div class="widget-link">Learn More <svg width="12" height="8" viewBox="0 0 12 8"><path d="M0 4h10M7 1l3 3-3 3" stroke="#f4412e" stroke-width="1.5" fill="none"/></svg></div>
  </section>

  <section class="widget fb">
    <div class="fb-head">Find us on Circlebook</div>
    <div class="fb-page"><div class="fb-mark"></div><div><div class="fb-name">GlimStep</div><span class="fb-like">Like</span></div></div>
    <div class="fb-count">207 people like <b>GlimStep</b></div>
    <div class="fb-faces">
      <div><div class="face" style="background:#b58a5e" role="img" aria-label="Follower photo"></div><div class="face-name">John Smith</div></div>
      <div><div class="face" style="background:#a86a3a" role="img" aria-label="Follower photo"></div><div class="face-name">Peter Doe</div></div>
      <div><div class="face" style="background:#5e5a4a" role="img" aria-label="Follower photo"></div><div class="face-name">Peter Doe</div></div>
      <div><div class="face" style="background:#3f6a5a" role="img" aria-label="Follower photo"></div><div class="face-name">James</div></div>
      <div><div class="face" style="background:#6a3a30" role="img" aria-label="Follower photo"></div><div class="face-name">John Smith</div></div>
      <div><div class="face" style="background:#3a5060" role="img" aria-label="Follower photo"></div><div class="face-name">Peter Doe</div></div>
      <div><div class="face" style="background:#d8c8a8" role="img" aria-label="Follower photo"></div><div class="face-name">Peter Doe</div></div>
      <div><div class="face" style="background:#8a4a6a" role="img" aria-label="Follower photo"></div><div class="face-name">James</div></div>
    </div>
    <div class="fb-foot"><i></i>Circlebook social plugin</div>
  </section>
</aside>

<footer class="site-footer">
  <div class="copy">All Right Reserved Copyright © 2014 &nbsp;-&nbsp; Terms and Conditions</div>
  <nav class="social" aria-label="Social links"><span></span><span></span><span></span><span></span></nav>
</footer>

</body>
</html>
```